Business card design Needed for new logo / Construction business, home extensions and new builds

We need a business card design using our new logo files which i will attach to this project :)

We are a small construction business specialising in home extensions, new builds and property development. We are very ambitious and would appreciate professional and elegant designs for our new business card.

Very serious about using the services on MakerQuarry and recently acquired our new logo from here :)

Please get involved, i will feedback when i can as i am very busy but can respond daily, thanks

Target Market(s)

People that want to build onto their houses, new building developments or adding too their existing property

Industry/Entity Type

Construction

Contact Information for Business Card

Renwick Tolliver Construction, Lionel Ashby (Managing Director), Tel 07822254961, email - info@renwick-tolliver, www.renwick-tolliver.co.uk

Colors

Designer to choose colors to be used in the design.

Requirements
Must have
• I like a deep grey on the back please. A lot of you have provided black from and back, try mixing things up a little. The black looks cool 😎 Thanks

```html
<!DOCTYPE html>
<html lang="en">
<head>
<meta charset="utf-8">
<title>Renwick Tolliver Construction – Business Card</title>
<link rel="stylesheet" href="https://fonts.googleapis.com/css2?family=Open+Sans:wght@400;600;700&display=swap">
<style>
  :root {
    --stage: #2b2b2d;
    --card-front: #1f1f22;
    --card-back: #242427;
    --silver: #d9dadc;
    --gold: #d9a53a;
    --gold-light: #f0c560;
    --gold-dark: #b8852a;
    --text: #f2f2f2;
    --shadow: rgba(0,0,0,0.45);
  }
  * { margin: 0; padding: 0; box-sizing: border-box; }
  html, body {
    width: 1200px; height: 780px; overflow: hidden;
    background: var(--stage);
    font-family: "Open Sans", Arial, sans-serif;
  }
  .canvas {
    position: relative; width: 1200px; height: 780px;
    display: flex; align-items: center; justify-content: center; gap: 50px;
  }
  .card {
    position: relative; width: 525px; height: 300px;
    border-radius: 22px; overflow: hidden;
    box-shadow: 0 14px 30px var(--shadow);
  }
  .card--front { background: var(--card-front); }
  .card--back { background: var(--card-back); display: flex; align-items: center; justify-content: center; }

  .brand { display: flex; align-items: center; gap: 10px; }
  .brand__mark { width: 12px; height: 12px; background: var(--gold); flex: none; }
  .brand__name {
    color: var(--silver); font-weight: 600; text-transform: uppercase;
    letter-spacing: 0.12em; line-height: 1.25;
  }
  .card--front .brand { position: absolute; left: 36px; top: 34px; }
  .card--front .brand__name { font-size: 15px; }
  .card--back .brand__name { font-size: 22px; }
  .card--back .brand__mark { width: 16px; height: 16px; }

  .contact {
    position: absolute; left: 36px; top: 118px;
    color: var(--text); font-size: 13px; line-height: 1.55;
    list-style: none;
  }
  .contact__address { margin-bottom: 6px; }
  .contact__line { display: flex; align-items: center; gap: 8px; }
  .contact__icon { width: 12px; height: 12px; flex: none; }

  .person {
    position: absolute; right: 52px; top: 150px; text-align: right;
  }
  .person__name { font-size: 27px; font-weight: 700; line-height: 1.1; }
  .person__first { color: var(--silver); }
  .person__last { color: var(--gold); }
  .person__role { color: var(--text); font-size: 15px; margin-top: 4px; }

  .accent-band {
    position: absolute; right: 0; top: 150px; width: 24px; height: 58px;
    background: linear-gradient(180deg, var(--gold-light), var(--gold-dark));
  }
</style>
</head>
<body>
<main class="canvas">

  <section class="card card--front" aria-label="Business card front">
    <div class="brand">
      <span class="brand__mark"></span>
      <span class="brand__name">Renwick Tolliver<br>Construction</span>
    </div>

    <ul class="contact">
      <li class="contact__address">Ashcombe Road, Westmoor<br>Fernbury, FB4 2LD</li>
      <li class="contact__line">
        <svg class="contact__icon" viewBox="0 0 12 12"><path fill="#d9a53a" d="M2.5 1l2 2.2-1 1.2a7 7 0 0 0 4.1 4.1l1.2-1 2.2 2-1.4 1.5C5.7 11 1 6.3.9 2.4z"/></svg>
        0782 225 4961
      </li>
      <li class="contact__line">
        <svg class="contact__icon" viewBox="0 0 12 12"><rect x="0.5" y="2" width="11" height="8" rx="1" fill="#d9a53a"/><path d="M1 2.6l5 3.8 5-3.8" stroke="#1f1f22" fill="none"/></svg>
        info@renwick-tolliver.co.uk
      </li>
      <li class="contact__line">
        <svg class="contact__icon" viewBox="0 0 12 12"><circle cx="6" cy="6" r="5.3" fill="none" stroke="#d9a53a" stroke-width="1.2"/><ellipse cx="6" cy="6" rx="2.3" ry="5.3" fill="none" stroke="#d9a53a"/><path d="M0.8 6h10.4" stroke="#d9a53a"/></svg>
        www.renwick-tolliver.co.uk
      </li>
    </ul>

    <div class="person">
      <p class="person__name"><span class="person__first">Lionel</span> <span class="person__last">Ashby</span></p>
      <p class="person__role">Managing Director</p>
    </div>

    <div class="accent-band" role="img" aria-label="Gold edge accent beside the name"></div>
  </section>

  <section class="card card--back" aria-label="Business card back">
    <div class="brand">
      <span class="brand__mark"></span>
      <span class="brand__name">Renwick Tolliver<br>Construction</span>
    </div>
  </section>

</main>
</body>
</html>
```